International Clinical Software Company needs a new business card design

We are looking for a new business card design for our company that has recently expanded into the UK market, making us a multinational company.
After having rebranded our website and produced a new style guide, we are looking for a business card that is creative and attention grabbing, while being consistent with the style and colour scheme used on the new website, www.plumvora.example
We produce care management technology for the aged care market, but the main aspect we aim to communicate is the human element of our software, and the way it assists in providing better care for aged people, and stronger relationships between aged people and the staff that care for them.
Our current business card is a dark green with gold text, which makes the text quite difficult to read, not very aesthetically appealing and the colour scheme looks quite dated.
We would like something fresh and modern, that can still be colourful but doesn't use large blocks of dark colour, and uses the colours within our logo.
Something tying in with the leaves that are used in our logo could work quite nicely, along with the Autumn/Fall colours of soft greens, yellows and reds (also in our existing logo). However also happy to look at fresh, completely out of the box ideas we may not have yet considered.
Target Market(s)
The people that receive this business card work in the aged card or health industry and are either corporate/management level staff or clinical (Registered Nurses, care workers etc.)
Industry/Entity Type
Health Product
Contact Information for Business Card
Company Name - BrindlewayCare
Company locations: United Kingdom, Australia, New Zealand
Staff Details:
Staff name: Derek Mallow
Staff job title: Executive Chairman
Staff email: d.mallow@plumvora.example
Office phone number: 01742 918576
Font styles to use
Other font styles liked:
- Calibri
Requirements
Must have
- Must include the BrindlewayCare brand name in it's current font
- Must include logo (3 leaves in gold circle)
- Must include Business Card Details
Nice to have
- Elements of gold
- White space
- Something autumn themed but not too cliched
Should not have
- No blue - used by a major competitor and we would like to differentiate from them
- Large blocks of dark green colour (the green that appears in our leaves on the logo on our current business card is the background colour and it is far too dark)

```html
<!DOCTYPE html>
<html lang="en">
<head>
<meta charset="utf-8">
<title>BrindlewayCare Business Card</title>
<link rel="stylesheet" href="https://fonts.googleapis.com/css2?family=Source+Sans+3:wght@400;600&display=swap">
<style>
  :root {
    --backdrop: #e6e6e4;
    --card-gold: #9d8862;
    --card-white: #f4f4f3;
    --ring-gold: #a38f69;
    --name-crimson: #a4143c;
    --detail-cream: #f5efe3;
    --brand-gold: #8f7a52;
  }
  * { margin: 0; padding: 0; box-sizing: border-box; }
  html, body {
    width: 1105px;
    height: 1200px;
    overflow: hidden;
    background: var(--backdrop);
    font-family: "Source Sans 3", "Carlito", sans-serif;
  }
  .business-card {
    position: absolute;
    left: 52px;
    top: 315px;
    width: 1000px;
    height: 570px;
    overflow: hidden;
  }
  .card-surface { position: absolute; inset: 0; }
  .contact-panel {
    position: absolute;
    left: 61px;
    top: 0;
    color: var(--detail-cream);
  }
  .staff-name {
    position: absolute;
    top: 122px;
    white-space: nowrap;
    font-size: 34px;
    font-weight: 600;
    color: var(--name-crimson);
  }
  .staff-title {
    position: absolute;
    top: 168px;
    white-space: nowrap;
    font-size: 27px;
  }
  .office-locations {
    position: absolute;
    top: 230px;
    white-space: nowrap;
    font-size: 27px;
    line-height: 37px;
  }
  .contact-list {
    position: absolute;
    top: 318px;
    list-style: none;
    font-size: 27px;
    line-height: 38px;
    white-space: nowrap;
  }
  .contact-item { display: flex; align-items: center; gap: 14px; }
  .contact-icon { width: 24px; height: 24px; flex: none; }
  .brand-lockup {
    position: absolute;
    left: 730px;
    top: 140px;
    transform: translateX(-50%);
    display: flex;
    flex-direction: column;
    align-items: center;
    gap: 26px;
  }
  .brand-dot {
    width: 128px;
    height: 128px;
    border-radius: 50%;
    border: 5px solid var(--brand-gold);
  }
  .brand-name {
    font-size: 50px;
    font-weight: 400;
    color: var(--brand-gold);
    white-space: nowrap;
    letter-spacing: 0.5px;
  }
</style>
</head>
<body>
  <div class="business-card">
    <svg class="card-surface" width="1000" height="570" viewBox="0 0 1000 570">
      <rect width="1000" height="570" fill="var(--card-gold)"/>
      <circle cx="730" cy="285" r="296" fill="none" stroke="var(--ring-gold)" stroke-width="3" opacity="0.9"/>
      <circle cx="730" cy="285" r="291" fill="none" stroke="var(--card-white)" stroke-width="3"/>
      <circle cx="730" cy="285" r="286" fill="var(--card-white)"/>
      <rect x="730" y="0" width="270" height="570" fill="var(--card-white)"/>
    </svg>

    <div class="contact-panel">
      <h1 class="staff-name">Derek Mallow</h1>
      <p class="staff-title">Executive Chairman</p>
      <p class="office-locations">United Kingdom,<br>Australia, New Zealand</p>
      <ul class="contact-list">
        <li class="contact-item">
          <svg class="contact-icon" viewBox="0 0 24 24" aria-hidden="true">
            <path fill="var(--name-crimson)" d="M6.6 3.5c.6-.5 1.4-.4 1.9.2l2 2.6c.4.5.4 1.3-.1 1.8L9.2 9.3c.9 2 2.5 3.6 4.5 4.5l1.2-1.2c.5-.5 1.3-.5 1.8-.1l2.6 2c.6.5.7 1.3.2 1.9l-1.4 1.8c-.7.8-1.9 1.1-2.9.7C10.3 17 7 13.7 5.1 8.8c-.4-1 0-2.2.8-2.9z"/>
          </svg>
          <span>01742 918576</span>
        </li>
        <li class="contact-item">
          <svg class="contact-icon" viewBox="0 0 24 24" aria-hidden="true">
            <rect x="3" y="6" width="18" height="12" rx="1.5" fill="var(--name-crimson)"/>
            <path d="M3.8 7l8.2 6 8.2-6" fill="none" stroke="var(--card-gold)" stroke-width="1.6"/>
          </svg>
          <span>d.mallow@plumvora.example</span>
        </li>
        <li class="contact-item">
          <svg class="contact-icon" viewBox="0 0 24 24" aria-hidden="true">
            <circle cx="12" cy="12" r="9" fill="var(--name-crimson)"/>
            <path d="M3.5 12h17M12 3.2c2.6 2.4 2.6 15.2 0 17.6M12 3.2c-2.6 2.4-2.6 15.2 0 17.6" fill="none" stroke="var(--card-gold)" stroke-width="1.3"/>
          </svg>
          <span>www.plumvora.example</span>
        </li>
      </ul>
    </div>

    <div class="brand-lockup">
      <div class="brand-dot"></div>
      <p class="brand-name">BrindlewayCare</p>
    </div>
  </div>
</body>
</html>
```